Tandem Hearth Works Pty Ltd

We need business cards for a company based in Perth, we install, service and maintain fire equipment.
On the front we want a great design with our logo and a small spot for our full company name, general company email address and office number. On the back we need space for our name, title, mobile number and email address on the back.

Target Market(s)

Facility managers and commercial/industrial building owners/occupiers.

Contact Information for Business Card

Font styles to use
Sans Serif

Requirements
Must have
• Please only submit 5 of your best samples.
Darker tones are preferred.
Nice to have
• We want to use, black, red and grey. Keep it modern and clean.
I've attached the company logo and a sample of a boarder we use on our emergency plans.
Should not have
• No preference. Let the designer choose.

```html
<!DOCTYPE html>
<html lang="en">
<head>
<meta charset="utf-8">
<title>Tandem Hearth Works Pty Ltd – Business Cards</title>
<link rel="stylesheet" href="https://fonts.googleapis.com/css2?family=Arimo:wght@400;700&display=swap">
<style>
  :root {
    --backdrop: #1c1c1c;
    --card: #0f0f0f;
    --red: #e31b23;
    --grey-light: #d2d2d2;
    --grey-mid: #bdbdbd;
    --divider: #4a4a4a;
    --card-w: 600px;
    --card-h: 343px;
  }
  * { box-sizing: border-box; margin: 0; padding: 0; }
  html, body {
    width: 1200px;
    height: 1015px;
    overflow: hidden;
  }
  body {
    background: var(--backdrop);
    font-family: "Arimo", Arial, sans-serif;
    position: relative;
  }
  .card {
    position: absolute;
    width: var(--card-w);
    height: var(--card-h);
    background: var(--card);
    border: 3px solid var(--red);
    box-shadow: 0 18px 40px rgba(0,0,0,0.6);
    display: flex;
    align-items: center;
  }
  .card--front { left: 110px; top: 140px; }
  .card--back { left: 490px; top: 540px; }

  .card__brand {
    width: 50%;
    padding: 0 28px;
    display: flex;
    justify-content: center;
    align-items: center;
  }
  .brand-name {
    color: var(--red);
    font-weight: 700;
    font-size: 26px;
    line-height: 1.2;
    text-align: center;
  }
  .card__divider {
    width: 1px;
    height: 140px;
    background: var(--divider);
    flex: none;
  }
  .card__details {
    width: 50%;
    padding-left: 34px;
    padding-right: 20px;
  }
  .company-name {
    color: var(--red);
    font-weight: 700;
    font-size: 21px;
    line-height: 1.1;
    text-transform: uppercase;
    margin-bottom: 12px;
  }
  .office-phone {
    color: var(--grey-light);
    font-weight: 700;
    font-size: 25px;
    letter-spacing: 0.5px;
    margin-bottom: 10px;
  }
  .person-name {
    color: var(--red);
    font-weight: 700;
    font-size: 23px;
    text-transform: uppercase;
    line-height: 1.1;
  }
  .person-title {
    color: var(--grey-mid);
    font-size: 15px;
    margin-bottom: 24px;
  }
  .contact-list { list-style: none; }
  .contact-item {
    display: flex;
    align-items: center;
    gap: 9px;
    color: var(--grey-mid);
    font-size: 14px;
    line-height: 1.65;
    white-space: nowrap;
  }
  .contact-item svg {
    width: 14px;
    height: 14px;
    flex: none;
  }
</style>
</head>
<body>

  <section class="card card--front" aria-label="Business card front">
    <div class="card__brand">
      <span class="brand-name">Tandem Hearth Works</span>
    </div>
    <div class="card__divider"></div>
    <div class="card__details">
      <h1 class="company-name">Tandem Hearth<br>Works Pty Ltd</h1>
      <p class="office-phone">789.4560.4560</p>
      <ul class="contact-list">
        <li class="contact-item">
          <svg viewBox="0 0 14 14" aria-hidden="true"><rect x="1" y="3" width="12" height="8" fill="var(--red)"/><path d="M1 3 L7 8 L13 3" stroke="var(--card)" stroke-width="1.2" fill="none"/></svg>
          info@tandemhearth.com
        </li>
        <li class="contact-item">
          <svg viewBox="0 0 14 14" aria-hidden="true"><g fill="none" stroke="var(--red)" stroke-width="1.2"><circle cx="7" cy="7" r="5.5"/><ellipse cx="7" cy="7" rx="2.4" ry="5.5"/><line x1="1.5" y1="7" x2="12.5" y2="7"/></g></svg>
          www.tandemhearth.com
        </li>
      </ul>
    </div>
  </section>

  <section class="card card--back" aria-label="Business card back">
    <div class="card__brand">
      <span class="brand-name">Tandem Hearth Works</span>
    </div>
    <div class="card__divider"></div>
    <div class="card__details">
      <h2 class="person-name">Marcus Hale</h2>
      <p class="person-title">Managing Director</p>
      <ul class="contact-list">
        <li class="contact-item">
          <svg viewBox="0 0 14 14" aria-hidden="true"><rect x="3.5" y="1" width="7" height="12" rx="1.2" fill="none" stroke="var(--red)" stroke-width="1.4"/><circle cx="7" cy="11" r="0.8" fill="var(--red)"/></svg>
          789.5612.5612
        </li>
        <li class="contact-item">
          <svg viewBox="0 0 14 14" aria-hidden="true"><rect x="1" y="3" width="12" height="8" fill="var(--red)"/><path d="M1 3 L7 8 L13 3" stroke="var(--card)" stroke-width="1.2" fill="none"/></svg>
          marcus@tandemhearth.com
        </li>
      </ul>
    </div>
  </section>

</body>
</html>
```